Business Card for beauty technology startup

Design Glimora Business Card for a Beauty, based on the website identity and colors (https://www.glimora-example.com).
Glimora is a beauty tech startup that gathers helpful product info for beauty lovers and consumers (such as availability on stores, price range and product reviews) for makeup products. The card design must be young, colorful but clean, and very modern.

Target Market(s)

woman, 15-35

Industry/Entity Type

Cosmetics

Contact Information for Business Card

Full Name, address, phone

Font styles to use
Other font styles liked:
• Advent Pro

Colors
e34297
86cfc6
ffffff
5c5c5c
e8e8e8
e667a6
b2b2b2

Requirements
Must have
• One full colored side with a creative design and another with card info
• Use Color palette: #95C5C5 and/or #D38AA5
• Use fonts: Advent Pro
• Use website identity: https://www.glimora-example.com
Nice to have
• If needed extra font: Roboto

```html
<!DOCTYPE html>
<html lang="en">
<head>
<meta charset="utf-8">
<title>Glimora Business Card</title>
<link rel="stylesheet" href="https://fonts.googleapis.com/css2?family=Advent+Pro:wght@300&family=Roboto:wght@400;500&display=swap">
<style>
  :root {
    --page-bg: #8a8a8a;
    --card-white: #f4f4f4;
    --rose: #b07789;
    --rose-line: #a9748a;
    --swoosh: #a8a8a8;
    --title-grey: #9a9a9a;
    --card-black: #18191b;
    --text-white: #ffffff;
  }
  * { box-sizing: border-box; margin: 0; padding: 0; }
  html, body { width: 1200px; height: 960px; overflow: hidden; }
  body { background: var(--page-bg); position: relative; font-family: "Roboto", sans-serif; }

  .card {
    position: absolute;
    width: 600px;
    height: 342px;
    border-radius: 18px;
    overflow: hidden;
  }
  .card-front { left: 314px; top: 113px; background: var(--card-white); }
  .card-back { left: 311px; top: 472px; height: 340px; background: var(--card-black); }

  .front-art { position: absolute; inset: 0; }

  .brand-mark {
    position: absolute;
    left: 14px; top: 34px;
    width: 212px; height: 212px;
    display: flex; align-items: center; justify-content: center;
    color: var(--rose);
    font-family: "Roboto", sans-serif;
    font-weight: 500;
    font-size: 34px;
  }

  .holder { position: absolute; left: 234px; top: 83px; }
  .holder-name { color: var(--rose); font-weight: 500; font-size: 20px; letter-spacing: 0.2px; }
  .holder-title { color: var(--title-grey); font-size: 15px; margin-top: 3px; }

  .contact {
    position: absolute; right: 27px; top: 202px;
    color: var(--text-white); font-size: 14.5px; text-align: right; line-height: 18px;
  }
  .address { margin-bottom: 12px; }
  .contact-line { display: flex; justify-content: flex-end; align-items: center; gap: 9px; height: 19px; }
  .contact-line svg { width: 13px; height: 13px; fill: var(--text-white); }

  .back-mark {
    position: absolute; left: 248px; top: 78px;
    width: 104px; height: 104px;
    border: 3px solid var(--rose-line); border-radius: 50%;
  }
  .back-name {
    position: absolute; left: 0; right: 0; top: 202px;
    text-align: center; color: var(--rose);
    font-family: "Advent Pro", sans-serif; font-weight: 300;
    font-size: 46px; letter-spacing: 6px;
  }
  .back-web {
    position: absolute; left: 0; right: 0; top: 294px;
    text-align: center; color: var(--text-white);
    font-size: 14px; letter-spacing: 4px;
  }
</style>
</head>
<body>
  <section class="card card-front">
    <svg class="front-art" viewBox="0 0 600 342" aria-hidden="true">
      <path d="M0,268 C230,284 470,212 600,70 L600,342 L0,342 Z" fill="var(--rose)"/>
      <path d="M190,272 C420,262 540,130 600,40 L600,60 C535,150 420,262 190,272 Z" fill="var(--swoosh)"/>
      <circle cx="120" cy="140" r="104" fill="none" stroke="var(--rose-line)" stroke-width="5"/>
    </svg>
    <div class="brand-mark">Glimora</div>

    <div class="holder">
      <div class="holder-name">MARA ELLISON</div>
      <div class="holder-title">CEO/FOUNDER</div>
    </div>

    <div class="contact">
      <div class="address">1420 Willow Crest Road<br>Juneau, Alaska 99801</div>
      <div class="contact-line">555 214 7730
        <svg viewBox="0 0 16 16"><path d="M3 1l3 0 1 4-2 1c1 2 3 4 5 5l1-2 4 1 0 3c0 1-1 2-2 2C7 15 1 9 1 3c0-1 1-2 2-2z"/></svg>
      </div>
      <div class="contact-line">555 382 6109
        <svg viewBox="0 0 16 16"><path d="M4 0h8a1 1 0 0 1 1 1v14a1 1 0 0 1-1 1H4a1 1 0 0 1-1-1V1a1 1 0 0 1 1-1zm1 2v10h6V2zm3 11a1 1 0 1 0 0 2 1 1 0 0 0 0-2z"/></svg>
      </div>
      <div class="contact-line">555 907 4428
        <svg viewBox="0 0 16 16"><path d="M4 1h8v4H4zM1 6h14v7h-3v2H4v-2H1zm4 5v3h6v-3z"/></svg>
      </div>
      <div class="contact-line">info@glimora-example.com
        <svg viewBox="0 0 16 16"><path d="M1 3h14v1L8 9 1 4zm0 3l7 5 7-5v7H1z"/></svg>
      </div>
    </div>
  </section>

  <section class="card card-back">
    <div class="back-mark"></div>
    <div class="back-name">GLIMORA</div>
    <div class="back-web">www.glimora-example.com</div>
  </section>
</body>
</html>
```